Homemaking training schools needs a Business Card design

Designer, Hello!

No special requirements, good-looking enough.
--------------------------------------------------------------------------

Name: Marcus Dole
Chairman
Tel: 0574-71948263
Mobile: 13857420916
Email: kelvora@mailnest.example
Web: www.prt2019.example
Add: No.258, LanpingJie, BeiyuanQu, Ningbo, Zhejiang

LOGO
Ningbo PRT Homemaking Training School

Target Market(s)

pregnant women, mothers, infants, the elderly and families, including cleaning, cooking, nursing training.

Industry/Entity Type

Business

Contact Information for Business Card

Name: Marcus Dole
Chairman
Tel: 0574-71948263
Mobile: 13857420916
Email: kelvora@mailnest.example
Web: www.prt2019.example

LOGO

Font styles to use
Serif
Sans Serif
Decorative

Requirements
Nice to have
• Feels: clean, specifications, safety, comfort, warmth and happiness.

```html
<!DOCTYPE html>
<html lang="en">
<head>
<meta charset="utf-8">
<title>PinRuiTang Training &amp; Services – Business Card</title>
<link rel="stylesheet" href="https://fonts.googleapis.com/css2?family=Lato:ital,wght@0,400;0,700;1,400&display=swap">
<style>
  :root {
    --brand-blue: #3a78bd;
    --brand-pink: #c4168f;
    --ink: #1c1c1c;
    --rule-dark: #333333;
    --paper: #ffffff;
    --backdrop: #e9eaec;
  }
  * { box-sizing: border-box; margin: 0; padding: 0; }
  html, body { width: 1200px; height: 900px; overflow: hidden; }
  body { background: var(--backdrop); position: relative; font-family: "Lato", sans-serif; color: var(--ink); }

  .card {
    position: absolute;
    width: 660px;
    height: 396px;
    overflow: hidden;
    box-shadow: 0 10px 28px rgba(0,0,0,.18);
  }

  /* ---------- shared brand block ---------- */
  .brand-name {
    font-family: "Lato", sans-serif;
    font-weight: 700;
    line-height: 1;
    white-space: nowrap;
  }
  .tagline-rule {
    display: flex; align-items: center; gap: 10px;
    font-family: "Lato", sans-serif; font-weight: 400; letter-spacing: .5px; white-space: nowrap;
  }
  .tagline-rule::before, .tagline-rule::after { content: ""; flex: 1; height: 1.5px; background: currentColor; }

  /* ---------- back side ---------- */
  .card-back { left: 460px; top: 30px; background: var(--brand-blue); color: var(--paper); }
  .card-back .brand { position: absolute; left: 0; right: 0; top: 122px; text-align: center; }
  .card-back .brand-name { font-size: 56px; color: var(--paper); }
  .card-back .tagline-rule { width: 470px; margin: 12px auto 0; font-size: 19px; color: var(--paper); }
  .card-back .web { position: absolute; left: 0; right: 0; top: 292px; text-align: center; font-size: 17px; letter-spacing: 3px; }

  /* ---------- front side ---------- */
  .card-front { left: 80px; top: 474px; background: var(--paper); }
  .card-front .swoosh { position: absolute; inset: 0; }
  .card-front .brand { position: absolute; left: 36px; top: 38px; width: 340px; }
  .card-front .brand-name { font-size: 44px; color: var(--brand-blue); }
  .card-front .tagline-rule { margin-top: 10px; font-size: 16px; color: var(--rule-dark); }

  .person { position: absolute; left: 40px; top: 152px; }
  .person .name { font-size: 26px; font-weight: 400; }
  .person .role { font-size: 17px; font-style: italic; color: var(--brand-blue); margin-top: 2px; }
  .address { position: absolute; left: 40px; top: 232px; font-size: 17px; line-height: 1.35; }

  .contacts { position: absolute; left: 300px; top: 286px; list-style: none; font-size: 17px; }
  .contacts li { display: flex; align-items: center; gap: 12px; height: 24px; }
  .contacts svg { width: 16px; height: 16px; fill: var(--brand-blue); flex: none; }
</style>
</head>
<body>

<section class="card card-back" aria-label="Business card, back">
  <div class="brand">
    <div class="brand-name">PinRuiTang</div>
    <div class="tagline-rule">Training &amp; Services</div>
  </div>
  <p class="web">www.prt2019.example</p>
</section>

<section class="card card-front" aria-label="Business card, front">
  <svg class="swoosh" viewBox="0 0 660 396" aria-hidden="true">
    <path d="M405 0 C560 70 636 210 646 396 L660 396 L660 0 Z" fill="var(--brand-blue)"/>
    <path d="M372 0 C540 74 616 220 626 396" fill="none" stroke="var(--brand-pink)" stroke-width="14"/>
  </svg>

  <div class="brand">
    <div class="brand-name">PinRuiTang</div>
    <div class="tagline-rule">Training &amp; Services</div>
  </div>

  <div class="person">
    <p class="name">Marcus Dole</p>
    <p class="role">Chairman</p>
  </div>

  <p class="address">No.258, LanpingJie<br>BeiyuanQu, Ningbo, Zhejiang</p>

  <ul class="contacts">
    <li><svg viewBox="0 0 16 16"><path d="M3 1l3 3-1.5 2a9 9 0 0 0 5.5 5.5L12 10l3 3-2 2C7 15 1 9 1 3z"/></svg>0574-71948263</li>
    <li><svg viewBox="0 0 16 16"><path d="M4 0h8a1 1 0 0 1 1 1v14a1 1 0 0 1-1 1H4a1 1 0 0 1-1-1V1a1 1 0 0 1 1-1zm1 2v9h6V2zm3 10.5a1 1 0 1 0 0 2 1 1 0 0 0 0-2z"/></svg>1385-7420916</li>
    <li><svg viewBox="0 0 16 16"><path d="M0 3h16v10H0zm1.5 1.2V5l6.5 4 6.5-4v-.8L8 8.2z"/></svg>kelvora@mailnest.example</li>
    <li><svg viewBox="0 0 16 16"><path d="M8 0a8 8 0 1 0 0 16A8 8 0 0 0 8 0zm0 1.5c.9 0 2 1.9 2.3 4.5H5.7C6 3.4 7.1 1.5 8 1.5zM1.6 7h2.9a14 14 0 0 0 0 2H1.6a6.5 6.5 0 0 1 0-2zm4 0h4.8a13 13 0 0 1 0 2H5.6a13 13 0 0 1 0-2zm5.9 0h2.9a6.5 6.5 0 0 1 0 2h-2.9a14 14 0 0 0 0-2zM5.7 10h4.6c-.3 2.6-1.4 4.5-2.3 4.5S6 12.6 5.7 10z"/></svg>www.prt2019.example</li>
  </ul>
</section>

</body>
</html>
```